Yacht, Boats, Watersports company needs a redesign of business card

Hello Designers!
We are a Boat dealership company that sells fun in the water, we sell boats, Yachts, Kayaks and also yacht WaterSport toys. We are looking to redesign our business cards in to something a little bit more sophisticated. in a way that we can make better use of our company colors. I'm attaching a zipped file containing the company 3 sets of company logo which one is an horizontal another one is a vertical and also a chromed 3d logo. Also is included two set of business cards that we use and also some designs that i think it's interesting. We use PMS 2026c Orange and PMS 7687C Blue. I would like to see at least two different options with the orange as accent and also using blue as an accent color. It's really important for the business cards to have a font option and size that is legible to most people. Our current website is wwww.coralpennant.com. Please visit if you want to have a better feeling of the Boat dealership
You can send Single sided or double side options. We are now using single sided but we may be open for a double side option if we really like the design.
Target Market(s)
Marine, boat sales, yacht sales, water toys sales/
Contact Information for Business Card
Name: Dale Whitcombe
Address: 212 North Fenwick Lane,
Palmetto Key, FL 33071
Phone: 954-731-8842
Fax: 954:731-8843
Cell: 954-382-1490
Email: dw@coralpennant.com
Website: coralpennant.com
Requirements
Must have
- the current information of the business card provided.
logo
use the PMS Colors
Nice to have
- a touch of elegance and sophistication but simple
Should not have
- should not have any typography that is hard to read, the card should be simple but yet sophisticated.

```html
<!DOCTYPE html>
<html lang="en">
<head>
<meta charset="utf-8">
<title>Coral Pennant — Business Card</title>
<link rel="stylesheet" href="https://fonts.googleapis.com/css2?family=Work+Sans:wght@400;500;600;700&display=swap">
<style>
  :root {
    --backdrop: #1c1c1c;
    --card: #262626;
    --card-edge: #2e2e2e;
    --orange: #f2622a;
    --blue: #1f5497;
    --ink: #f2f2f2;
  }
  * { margin: 0; padding: 0; box-sizing: border-box; }
  html, body { width: 1200px; height: 900px; overflow: hidden; }
  body {
    background: var(--backdrop);
    font-family: "Work Sans", Arial, sans-serif;
    color: var(--ink);
    display: flex;
    flex-direction: column;
    align-items: center;
    justify-content: center;
    gap: 30px;
  }
  .card {
    position: relative;
    width: 700px;
    height: 400px;
    background: linear-gradient(135deg, var(--card) 0%, var(--card-edge) 100%);
    border-bottom: 6px solid var(--orange);
    box-shadow: 0 14px 30px rgba(0,0,0,.55);
  }
  .brand {
    display: flex;
    flex-direction: column;
    align-items: center;
    gap: 14px;
  }
  .brand-mark {
    width: 80px; height: 80px;
    border: 6px solid var(--orange);
    border-radius: 50%;
  }
  .brand-name {
    font-weight: 600;
    font-size: 36px;
    letter-spacing: 3.5px;
    text-transform: uppercase;
    color: var(--blue);
    white-space: nowrap;
  }
  .card-front {
    display: flex;
    align-items: center;
    justify-content: center;
  }
  .card-front .brand { margin-top: -20px; }

  .card-back { display: flex; align-items: center; }
  .card-back .brand { width: 360px; flex: none; }
  .card-back .brand-mark { width: 62px; height: 62px; border-width: 5px; }
  .card-back .brand-name { font-size: 24px; letter-spacing: 2.5px; }
  .divider {
    width: 2px;
    height: 200px;
    flex: none;
    background: var(--orange);
  }
  .contact { padding-left: 26px; }
  .contact-name {
    font-weight: 700;
    font-size: 28px;
    letter-spacing: 2px;
    text-transform: uppercase;
    color: var(--orange);
    white-space: nowrap;
    margin-bottom: 6px;
  }
  .contact-address, .contact-line {
    font-size: 16px;
    letter-spacing: .8px;
    line-height: 1.42;
    white-space: nowrap;
  }
  .contact-address { margin-bottom: 2px; }
  .contact-line { display: flex; align-items: center; gap: 8px; }
  .contact-line svg { width: 13px; height: 13px; flex: none; }
  .highlight { color: var(--orange); }
</style>
</head>
<body>
  <section class="card card-front">
    <div class="brand">
      <span class="brand-mark"></span>
      <span class="brand-name">Coral Pennant</span>
    </div>
  </section>

  <section class="card card-back">
    <div class="brand">
      <span class="brand-mark"></span>
      <span class="brand-name">Coral Pennant</span>
    </div>
    <div class="divider"></div>
    <div class="contact">
      <h1 class="contact-name">Dale Whitcombe</h1>
      <p class="contact-address">212 North Fenwick Lane,<br>Palmetto Key, FL 33071</p>
      <p class="contact-line">
        <svg viewBox="0 0 16 16" aria-hidden="true"><path fill="#f2622a" d="M4 1l3 3-2 2c1 2 3 4 5 5l2-2 3 3-2 3C7 15 1 9 1 3z"/></svg>
        954-731-8842
      </p>
      <p class="contact-line">
        <svg viewBox="0 0 16 16" aria-hidden="true"><rect x="4" y="1" width="8" height="4" fill="#f2622a"/><rect x="1" y="6" width="14" height="6" rx="1" fill="#f2622a"/><rect x="4" y="10" width="8" height="5" fill="#f2622a" stroke="#262626"/></svg>
        954:731-8843
      </p>
      <p class="contact-line">
        <svg viewBox="0 0 16 16" aria-hidden="true"><rect x="4" y="1" width="8" height="14" rx="1.5" fill="none" stroke="#f2622a" stroke-width="1.6"/></svg>
        954-382-1490
      </p>
      <p class="contact-line">
        <svg viewBox="0 0 16 16" aria-hidden="true"><rect x="1" y="3" width="14" height="10" fill="none" stroke="#f2622a" stroke-width="1.4"/><path d="M1 3l7 6 7-6" fill="none" stroke="#f2622a" stroke-width="1.4"/></svg>
        dw@coralpennant.com
      </p>
      <p class="contact-line">
        <svg viewBox="0 0 16 16" aria-hidden="true"><circle cx="8" cy="8" r="6.5" fill="none" stroke="#f2622a" stroke-width="1.3"/><ellipse cx="8" cy="8" rx="3" ry="6.5" fill="none" stroke="#f2622a" stroke-width="1.1"/><path d="M1.5 8h13" stroke="#f2622a" stroke-width="1.1"/></svg>
        <span>www.<span class="highlight">coralpennant</span>.com</span>
      </p>
    </div>
  </section>
</body>
</html>
```